Architectural, Engineering and Design Build

Tovandex4.com
Veteran Disabled Certified company is doing business in Architecture, Engineer and Design build - look simialr websites and come up with design follow following website
https://hollis-darnet.example/
https://www.venlorcogroup.example/
https://www.pembrisgc.example/contract-vehicles/service-disabled-veteran-owned-small-business-sdvosb/
https://www.corbelnetlink.example/about/sdvosb/

Target Market(s)

US - Defense and Federal Government

Industry/Entity Type

Colors
0054AA
0677BA
7BADD7
CADEEF
E8F1F8

Requirements
Must have
• Army, American patriotism , Buildings, construction, architecture, engineering
Nice to have
• I need to attract federal government agencies and Defense

```html
<!DOCTYPE html>
<html lang="en">
<head>
<meta charset="utf-8">
<title>Tovandex4 Architectural Engineering Construction</title>
<link href="https://fonts.googleapis.com/css2?family=Outfit:wght@400;500;600;700;800&display=swap" rel="stylesheet">
<style>
:root{
  --blue-900:#0054AA;
  --blue-700:#0677BA;
  --blue-400:#7BADD7;
  --blue-200:#CADEEF;
  --blue-100:#E8F1F8;
  --ink:#1b1b1b;
  --text:#333;
  --white:#fff;
}
*{margin:0;padding:0;box-sizing:border-box}
html,body{width:1200px;height:4474px;overflow:hidden}
body{position:relative;font-family:"Outfit",sans-serif;color:var(--text);background:var(--white)}
.abs{position:absolute}
svg{display:block}

/* hero */
.hero{left:0;top:0;width:1200px;height:582px;
  background:
    radial-gradient(ellipse 420px 260px at 72% 62%,rgba(214,192,160,.55),rgba(214,192,160,0)),
    radial-gradient(ellipse 300px 200px at 90% 30%,rgba(40,45,55,.7),rgba(40,45,55,0)),
    linear-gradient(180deg,#3b4a63 0%,#55647a 30%,#857b6d 62%,#4a443c 85%,#2c2a27 100%)}
.hero-shade{left:0;top:0;width:760px;height:582px;background:linear-gradient(90deg,rgba(15,25,45,.8),rgba(15,25,45,.35) 60%,rgba(15,25,45,0))}
.brand{display:flex;align-items:center;gap:8px;font-weight:800;font-size:24px;letter-spacing:.5px}
.brand .mark{width:34px;height:34px;border-radius:50%;background:var(--blue-900)}
.brand-top{left:140px;top:50px;color:var(--white)}
.brand-top .mark{background:var(--white)}
.nav{top:58px;font-size:15px;color:var(--white);font-weight:500}
.nav-contact{left:936px;top:47px;width:122px;height:42px;background:var(--white);color:var(--blue-900);font-size:15px;display:flex;align-items:center;justify-content:center}
.hero-title{left:141px;top:220px;color:var(--white);font-size:34px;font-weight:700;line-height:48px;text-transform:uppercase}
.hero-text{left:141px;top:325px;width:380px;color:var(--white);font-size:14px;line-height:28px}
.btn-outline{display:flex;align-items:center;justify-content:center;font-size:15px;font-weight:500}
.hero-btn{left:142px;top:424px;width:183px;height:42px;border:1.5px solid var(--white);color:var(--white)}
.slide-prev{left:1097px;top:530px;width:51px;height:52px;background:var(--white)}
.slide-next{left:1148px;top:530px;width:52px;height:52px;background:var(--blue-700)}
.slide-prev svg,.slide-next svg{margin:16px auto}

/* headings */
.sec-title{font-size:32px;font-weight:700;color:var(--ink);text-transform:uppercase;text-align:center;width:1200px;left:0}
.sec-sub{left:320px;width:560px;text-align:center;font-size:14.5px;line-height:24px;color:var(--ink)}

/* services */
.svc-main{left:141px;top:804px;width:455px;height:363px;
  background:
    radial-gradient(ellipse 40px 130px at 51% 72%,rgba(150,100,60,.75),rgba(150,100,60,0)),
    linear-gradient(180deg,#eceef0 0%,#e0e3e6 28%,#a6a39a 48%,#6d6962 75%,#8a857c 100%)}
.svc-icon{left:660px;top:847px}
.svc-head{left:658px;top:942px;font-size:15.5px;font-weight:600;color:var(--ink)}
.svc-list{left:658px;top:982px;list-style:none;font-size:13.5px;color:var(--ink)}
.svc-list li{display:flex;align-items:center;gap:8px;height:40px}
.card{top:1224px;width:294px;height:228px}
.card p{position:absolute;left:22px;bottom:28px;width:240px;color:var(--white);font-size:12.5px;line-height:20px}
.card-tower{background:linear-gradient(180deg,#c2b7a2 0%,#8b826f 45%,#4a453e 75%,#22201e 100%)}
.card-hall{background:
    radial-gradient(ellipse 60px 40px at 48% 22%,rgba(170,60,60,.6),rgba(170,60,60,0)),
    linear-gradient(180deg,#caa970 0%,#8a7350 45%,#3e3730 75%,#1e1c1a 100%)}
.card-dome{background:linear-gradient(180deg,#a4acb6 0%,#7d838b 40%,#53564f 70%,#232426 100%)}

/* why */
.why{left:0;top:1539px;width:1200px;height:460px;
  background:
    radial-gradient(ellipse 300px 220px at 50% 40%,rgba(120,160,215,.35),rgba(120,160,215,0)),
    linear-gradient(180deg,rgba(30,100,185,.93),rgba(20,90,175,.95)),
    linear-gradient(90deg,#5d7aa8,#8aa0c4,#5d7aa8)}
.why .sec-title{color:var(--white);top:58px}
.why-sub{left:355px;top:100px;width:490px;text-align:center;color:var(--white);font-size:12.5px;line-height:20px}
.feat{width:300px;text-align:center;color:var(--white)}
.feat .ring{width:100px;height:100px;border:2.5px solid var(--white);border-radius:50%;margin:0 auto;display:flex;align-items:center;justify-content:center}
.feat h3{margin-top:28px;font-size:15px;font-weight:600}
.feat p{margin:10px auto 0;width:260px;font-size:11.5px;line-height:19px}

/* about */
.about-bg{left:0;top:1999px;width:1200px;height:1110px;overflow:hidden}
.about-h{left:141px;top:2222px;font-size:25px;font-weight:700;color:var(--ink);line-height:32px}
.about-p{left:141px;top:2300px;width:400px;font-size:14.5px;line-height:24px;color:var(--ink)}
.mission{left:141px;top:2416px;font-size:18px;font-weight:600;color:var(--ink)}
.bullet{display:flex;align-items:center;gap:8px;font-size:13px;color:var(--ink)}
.read-more{left:142px;top:2513px;width:117px;height:43px;border:1.5px solid var(--blue-900);color:var(--blue-900);background:var(--white)}
.about-frame{left:662px;top:2150px;width:418px;height:429px;background:var(--white);box-shadow:0 4px 18px rgba(0,40,90,.12)}
.about-img{left:604px;top:2171px;width:455px;height:444px;
  background:
    radial-gradient(ellipse 150px 170px at 58% 45%,rgba(238,236,230,.95),rgba(238,236,230,0)),
    linear-gradient(180deg,#a9c7e6 0%,#cfe0ef 30%,#e8ecee 55%,#b8b6af 80%,#6f6d67 100%)}

/* team */
.team-title{left:144px;top:2686px;font-size:25px;font-weight:700;color:var(--ink)}
.arr{width:35px;height:35px;display:flex;align-items:center;justify-content:center}
.arr.light{background:var(--blue-100)}
.arr.dark{background:var(--blue-700)}
.member{top:2763px;width:222px}
.member .pic{height:267px}
.member h4{margin-top:18px;text-align:center;font-size:12.5px;font-weight:600;color:var(--ink)}
.member span{display:block;text-align:center;margin-top:6px;font-size:11.5px;color:var(--text)}
.pic-1{background:linear-gradient(180deg,#c6cacd 0%,#9aa4ad 40%,#3c5668 70%,#2a3b48 100%)}
.pic-2{background:linear-gradient(180deg,#b7b397 0%,#98978c 35%,#555454 65%,#2b2b2d 100%)}
.pic-3{background:linear-gradient(180deg,#56644f 0%,#7a8276 40%,#8d9095 70%,#5f6367 100%)}
.pic-4{background:linear-gradient(180deg,#b88470 0%,#c9b1a3 35%,#ecebe8 60%,#5f7a96 100%)}

/* testimonials */
.testi-title{left:141px;top:3178px;font-size:31px;font-weight:700;color:var(--ink)}
.t-next{left:186px;top:3327px;width:62px;height:63px;background:var(--blue-900);display:flex;align-items:center;justify-content:center}
.t-prev{left:186px;top:3404px;width:62px;height:62px;background:var(--blue-100);display:flex;align-items:center;justify-content:center}
.t-big{left:304px;top:3279px;width:264px;height:406px;background:linear-gradient(180deg,#6f8a4e 0%,#a0ad84 28%,#e6e4e2 52%,#3d4458 82%,#2c3140 100%)}
.t-small{top:3522px;width:151px;height:163px}
.ts-1{background:linear-gradient(180deg,#c0bbb1 0%,#857a6d 50%,#3a332d 80%,#2a2622 100%)}
.ts-2{background:linear-gradient(180deg,#e8e6e2 0%,#c9cdd3 40%,#8ea6c6 70%,#4b6a96 100%)}
.ts-3{background:linear-gradient(180deg,#c08a5a 0%,#a06a46 40%,#6a4a3a 65%,#2f4f8a 100%)}
.ts-4{background:linear-gradient(180deg,#efefed 0%,#e2d6d2 50%,#d9a4a8 75%,#c2727c 100%)}
.quote{left:608px;top:3296px}
.t-name{left:608px;top:3342px;font-size:18px;font-weight:700;color:var(--blue-900)}
.t-co{left:608px;top:3378px;font-size:12.5px;font-weight:600;color:var(--ink)}
.t-text{left:608px;top:3402px;width:450px;font-size:13px;line-height:23px;color:var(--ink)}

/* cta */
.cta{left:0;top:3772px;width:1200px;height:279px;background:linear-gradient(180deg,rgba(20,95,185,.93),rgba(15,85,170,.95)),linear-gradient(90deg,#7f93b4,#aebbd0)}
.cta h2{position:absolute;left:0;top:70px;width:1200px;text-align:center;color:var(--white);font-size:26px;font-weight:700;text-transform:uppercase}
.cta p{position:absolute;left:0;top:119px;width:1200px;text-align:center;color:var(--white);font-size:13.5px;font-weight:500}
.cta .btn-outline{position:absolute;left:509px;top:158px;width:180px;height:42px;border:1.5px solid var(--white);color:var(--white)}

/* footer */
.f-head{top:4134px;font-size:22px;font-weight:700;color:var(--blue-900)}
.f-links{left:155px;top:4186px;list-style:none;font-size:14px;font-weight:500;color:var(--ink)}
.f-links li{height:38px}
.f-row{left:438px;display:flex;gap:18px;font-size:14px;font-weight:500;color:var(--ink);line-height:22px}
.brand-foot{left:850px;top:4192px;color:var(--blue-900);font-size:26px}
.f-tag{left:798px;top:4294px;font-size:13.5px;font-weight:500;color:var(--ink)}
.social{top:4331px;width:32px;height:32px;border:2px solid var(--blue-900);border-radius:50%}
.copy{left:0;top:4423px;width:1200px;height:51px;background:var(--blue-900);color:var(--white);font-size:12px;display:flex;align-items:center;justify-content:center}
</style>
</head>
<body>

<!-- HERO -->
<div class="abs hero" role="img" aria-label="Federal government building at dusk with flag on the roof"></div>
<div class="abs hero-shade"></div>
<div class="abs brand brand-top"><span class="mark"></span>TOVANDEX4</div>
<a class="abs nav" style="left:518px">Home</a>
<a class="abs nav" style="left:600px">About US</a>
<a class="abs nav" style="left:703px">Services</a>
<a class="abs nav" style="left:800px">Why Choose Us</a>
<a class="abs nav-contact">Contact</a>
<h1 class="abs hero-title">Building for the future<br>of defense</h1>
<p class="abs hero-text">Pioneering the development of advanced, resilient, and Sustainable defense infrastructure to meet future challenges.</p>
<a class="abs btn-outline hero-btn">Explore Our Services</a>
<div class="abs slide-prev"><svg width="20" height="20" viewBox="0 0 20 20"><path d="M13 3 6 10l7 7" fill="none" stroke="#222" stroke-width="2"/></svg></div>
<div class="abs slide-next"><svg width="20" height="20" viewBox="0 0 20 20"><path d="M7 3l7 7-7 7" fill="none" stroke="#fff" stroke-width="2"/></svg></div>

<!-- SERVICES -->
<h2 class="abs sec-title" style="top:660px">Our Services</h2>
<p class="abs sec-sub" style="top:710px">Lorem ipsum dolor sit amet, consectetur adipiscing elit, sed do eiusmod tempor aliqua Quis ipsum.</p>
<div class="abs svc-main" role="img" aria-label="Man in coat standing before a columned government building"></div>
<svg class="abs svc-icon" width="60" height="74" viewBox="0 0 60 74" fill="none" stroke="#111" stroke-width="2.5">
  <rect x="3" y="3" width="48" height="66" rx="3"/>
  <path d="M11 30V18M19 30V12M27 30V20M35 30V14M43 30V22"/>
  <rect x="10" y="40" width="8" height="8"/><rect x="10" y="54" width="8" height="8"/>
  <path d="M24 44h16M24 58h12"/>
  <circle cx="50" cy="56" r="8" fill="#fff"/><path d="M46 56l3 3 5-6"/>
</svg>
<h3 class="abs svc-head">Clear and concise descriptions</h3>
<ul class="abs svc-list">
  <li><svg width="18" height="18" viewBox="0 0 18 18"><path d="M2 2l14 7-14 7 4-7z" fill="none" stroke="#111" stroke-width="1.6"/></svg>Core architectural</li>
  <li><svg width="18" height="18" viewBox="0 0 18 18"><path d="M2 2l14 7-14 7 4-7z" fill="none" stroke="#111" stroke-width="1.6"/></svg>Engineering</li>
  <li><svg width="18" height="18" viewBox="0 0 18 18"><path d="M2 2l14 7-14 7 4-7z" fill="none" stroke="#111" stroke-width="1.6"/></svg>Design-build services</li>
  <li><svg width="18" height="18" viewBox="0 0 18 18"><path d="M2 2l14 7-14 7 4-7z" fill="none" stroke="#111" stroke-width="1.6"/></svg>Defense and government sector</li>
</ul>
<div class="abs card card-tower" style="left:141px" role="img" aria-label="Tall office tower viewed from street level"><p>Lorem ipsum dolor sit amet, consectetur adipiscing elit, sed do.</p></div>
<div class="abs card card-hall" style="left:453px" role="img" aria-label="Grand hall interior with American flag hanging"><p>Lorem ipsum dolor sit amet, consectetur adipiscing elit, sed do.</p></div>
<div class="abs card card-dome" style="left:764px" role="img" aria-label="Domed capitol building under cloudy sky"><p>Lorem ipsum dolor sit amet, consectetur adipiscing elit, sed do.</p></div>

<!-- WHY CHOOSE US -->
<section class="abs why" aria-label="Why choose us">
  <h2 class="abs sec-title">Why Choose Us?</h2>
  <p class="abs why-sub">Lorem ipsum dolor sit amet, consectetur adipiscing elit, sed do eiusmod tempor aliqua Quis ipsum.</p>
  <div class="abs feat" style="left:124px;top:181px">
    <div class="ring"><svg width="52" height="52" viewBox="0 0 52 52" fill="none" stroke="#fff" stroke-width="2"><path d="M6 28l10-10 10 6 10-6 10 10-12 12-8-6-8 6z"/><path d="M20 24l6 4"/></svg></div>
    <h3>Veteran-Owned Business</h3>
    <p>Lorem Ipsum is simply dummy text of the printing and typesetting industry. Lorem Ipsum has been the industry's ever</p>
  </div>
  <div class="abs feat" style="left:446px;top:181px">
    <div class="ring"><svg width="52" height="52" viewBox="0 0 52 52" fill="none" stroke="#fff" stroke-width="2"><circle cx="26" cy="14" r="6"/><path d="M16 34c0-7 4-12 10-12s10 5 10 12"/><path d="M8 44l3-3 3 3M23 44l3-3 3 3M38 44l3-3 3 3"/></svg></div>
    <h3>Experience and Expertise</h3>
    <p>Lorem Ipsum is simply dummy text of the printing and typesetting industry. Lorem Ipsum has been the industry's ever</p>
  </div>
  <div class="abs feat" style="left:765px;top:181px">
    <div class="ring"><svg width="52" height="52" viewBox="0 0 52 52" fill="none" stroke="#fff" stroke-width="2"><circle cx="28" cy="16" r="9"/><path d="M24 16l3 3 5-6"/><path d="M8 40l8-6h12l-6 4h10l10-8"/></svg></div>
    <h3>Commitment to Quality</h3>
    <p>Lorem Ipsum is simply dummy text of the printing and typesetting industry. Lorem Ipsum has been the industry's ever</p>
  </div>
</section>

<!-- ABOUT -->
<div class="abs about-bg">
  <svg width="1200" height="1110" viewBox="0 0 1200 1110">
    <polygon points="0,0 380,0 0,380" fill="#E8F1F8"/>
    <polygon points="1200,0 780,0 1200,420" fill="#E8F1F8"/>
    <polygon points="0,560 240,1110 0,1110" fill="#E8F1F8"/>
    <polygon points="1200,620 1200,1000 1000,820" fill="#E8F1F8" opacity=".7"/>
  </svg>
</div>
<h2 class="abs sec-title" style="top:2076px">About Us</h2>
<h3 class="abs about-h">TOVANDEX4 ARCHITECTURAL<br>ENGINEERING</h3>
<p class="abs about-p">Lorem Ipsum is simply dummy text of the printing and typesetting industry. Lorem Ipsum has been the industry's standard dummy text ever since the 1500s, when an remaining essentially unchanged.</p>
<h4 class="abs mission">Mission Statement</h4>
<div class="abs bullet" style="left:141px;top:2462px"><svg width="18" height="18" viewBox="0 0 18 18"><path d="M2 2l14 7-14 7 4-7z" fill="none" stroke="#111" stroke-width="1.6"/></svg>Company's mission</div>
<div class="abs bullet" style="left:318px;top:2462px"><svg width="18" height="18" viewBox="0 0 18 18"><path d="M2 2l14 7-14 7 4-7z" fill="none" stroke="#111" stroke-width="1.6"/></svg>Values</div>
<a class="abs btn-outline read-more">Read More</a>
<div class="abs about-frame"></div>
<div class="abs about-img" role="img" aria-label="Capitol dome with columned wing under a pale blue sky"></div>

<!-- TEAM -->
<h2 class="abs team-title">OUR TEAM</h2>
<div class="abs arr light" style="left:976px;top:2685px"><svg width="12" height="12" viewBox="0 0 12 12"><path d="M8 1 3 6l5 5" fill="none" stroke="#0054AA" stroke-width="1.6"/></svg></div>
<div class="abs arr dark" style="left:1023px;top:2685px"><svg width="12" height="12" viewBox="0 0 12 12"><path d="M4 1l5 5-5 5" fill="none" stroke="#fff" stroke-width="1.6"/></svg></div>
<div class="abs member" style="left:141px"><div class="pic pic-1" role="img" aria-label="Team member portrait, man in blue blazer"></div><h4>Lorem ipsum dolor</h4><span>Lorem ipsum dolor sit amet,</span></div>
<div class="abs member" style="left:373px"><div class="pic pic-2" role="img" aria-label="Team member portrait, woman in black top"></div><h4>Lorem ipsum dolor</h4><span>Lorem ipsum dolor sit amet,</span></div>
<div class="abs member" style="left:605px"><div class="pic pic-3" role="img" aria-label="Team member portrait, man in grey cardigan"></div><h4>Lorem ipsum dolor</h4><span>Lorem ipsum dolor sit amet,</span></div>
<div class="abs member" style="left:837px"><div class="pic pic-4" role="img" aria-label="Team member portrait, woman in white t-shirt"></div><h4>Lorem ipsum dolor</h4><span>Lorem ipsum dolor sit amet,</span></div>

<!-- TESTIMONIALS -->
<h2 class="abs testi-title">CLIENT TESTIMONIALS</h2>
<div class="abs t-next"><svg width="18" height="18" viewBox="0 0 18 18"><path d="M6 2l7 7-7 7" fill="none" stroke="#fff" stroke-width="2"/></svg></div>
<div class="abs t-prev"><svg width="18" height="18" viewBox="0 0 18 18"><path d="M12 2 5 9l7 7" fill="none" stroke="#333" stroke-width="2"/></svg></div>
<div class="abs t-small ts-1" style="left:141px" role="img" aria-label="Client portrait, man with glasses"></div>
<div class="abs t-big" role="img" aria-label="Featured client portrait, woman in white top outdoors"></div>
<div class="abs t-small ts-2" style="left:582px" role="img" aria-label="Client portrait, man in plaid shirt"></div>
<div class="abs t-small ts-3" style="left:745px" role="img" aria-label="Client portrait, smiling woman"></div>
<div class="abs t-small ts-4" style="left:908px" role="img" aria-label="Client portrait, young man in pink shirt"></div>
<svg class="abs quote" width="46" height="36" viewBox="0 0 46 36" fill="#0054AA"><circle cx="10" cy="10" r="9"/><path d="M19 10c0 12-6 20-16 24l-2-3c7-4 10-10 10-17z"/><circle cx="34" cy="10" r="9"/><path d="M43 10c0 12-6 20-16 24l-2-3c7-4 10-10 10-17z"/></svg>
<h3 class="abs t-name">Marcus Delhaven</h3>
<p class="abs t-co">Tovandex4 Architectural Engineering</p>
<p class="abs t-text">Lorem Ipsum is simply dummy text of the printing and typesetting industry. Lorem Ipsum has been the industry's standard dummy text ever since the 1500s, when an unknown printer took a galley of type and scrambled it to make a type specimen book.</p>

<!-- CTA -->
<section class="abs cta" aria-label="Request a quote">
  <h2>Tovandex4 Architectural Engineering Construction</h2>
  <p>Lorem Ipsum is simply dummy text of the printing and typesetting industry.</p>
  <a class="btn-outline">Request A Quote</a>
</section>

<!-- FOOTER -->
<h3 class="abs f-head" style="left:155px">Quick links</h3>
<ul class="abs f-links">
  <li>Home</li><li>About Us</li><li>Services</li><li>Why Choose Us</li><li>Contact</li>
</ul>
<h3 class="abs f-head" style="left:438px">Contact Info</h3>
<div class="abs f-row" style="top:4192px">
  <svg width="20" height="24" viewBox="0 0 20 24"><path d="M10 1a8 8 0 0 0-8 8c0 6 8 14 8 14s8-8 8-14a8 8 0 0 0-8-8z" fill="none" stroke="#111" stroke-width="2"/><circle cx="10" cy="9" r="3" fill="#111"/></svg>
  <span style="width:260px">Lorem Ipsum is simply dummy text of the printing and typesetting industry</span>
</div>
<div class="abs f-row" style="top:4277px">
  <svg width="20" height="20" viewBox="0 0 20 20"><path d="M4 1h4l2 5-3 2a11 11 0 0 0 5 5l2-3 5 2v4c0 1-1 2-2 2A17 17 0 0 1 2 3c0-1 1-2 2-2z" fill="#111"/></svg>
  <span>(123) 456-789</span>
</div>
<div class="abs f-row" style="top:4323px">
  <svg width="20" height="20" viewBox="0 0 20 20"><rect x="1" y="4" width="18" height="12" fill="none" stroke="#111" stroke-width="2"/><path d="M1 4l9 7 9-7" fill="none" stroke="#111" stroke-width="2"/></svg>
  <span>info@tovandex4architectural.example</span>
</div>
<div class="abs brand brand-foot"><span class="mark"></span>TOVANDEX4</div>
<p class="abs f-tag">Architectural Engineering Construction</p>
<span class="abs social" style="left:889px" aria-label="Social profile"></span>
<span class="abs social" style="left:936px" aria-label="Social profile"></span>
<div class="abs copy">© 2024 Copyright Tovandex4 Architectural Engineering Construction. All Rights</div>

</body>
</html>
```